High End Cosmetic Packaging Design Project

Looking for packaging for 2 products for a High end skin care line aimed at the 35+ year old women. Color scheme is Pantone 2765c with accents of metallic silver, copper or gold, Pantone colors 871-877c. Possible watermark in the background or a 3D image. We are open to any good ideas and suggestions. Box dimensions for the 2 products are small, approximately 4.375 inches high and 1.5 inches square. I have attached an image of the logo. I have the logo files in all the various forms. 1 box is for a Vitamin C Serum and the other box is for an Anti Aging Serum. Boxes are the same but the text will be different on both products. I will supply the text for the boxes later, including directions & ingredients and a UPC code that has to go on the underside of the box. It has to be an elegant design that will stand out in photos online. Good and quick communication & feedback between you and us is essential. I have attached a jpg of our new logo. I have this logo in all available forms
*****We are open to all ideas and want your ideas and input. The bottles that go inside these boxes are a deep violet almost black tavlen glass. This is where the pantone color selection came from but upon further thought it may not be the right choice. We were out looking at cosmetic packaging today and thought also as an idea that a dark charcoal, or black box might work as well. We have seen boxes in those dark shades in glossy, matt and some with a sparkle finish. Embossed lettering may be a possibility as well. Copper letters may be an idea that works well also. These are just ideas rolling aroung in our heads but please give us your ideas*******
This is for the 35+ year old woman.
Communication

```html
<!DOCTYPE html>
<html lang="en">
<head>
<meta charset="utf-8">
<title>Serum Carton Dielines</title>
<link rel="stylesheet" href="https://fonts.googleapis.com/css2?family=Quicksand:wght@300;400&display=swap">
<style>
  :root {
    --paper: #ffffff;
    --dieline: #a9a9ad;
    --fold: #b9b9bd;
    --navy: #19165a;
    --silver-light: #dedfe2;
    --silver-dark: #a3a4a8;
    --gold-light: #cdbfa2;
    --gold-dark: #9f8d63;
    --silver-text: #b4b5b8;
    --gold-text: #a8976e;
  }
  html, body {
    margin: 0;
    width: 1200px;
    height: 754px;
    overflow: hidden;
    background: var(--paper);
  }
  .sheet { display: block; width: 1200px; height: 754px; }
  .carton-outline { fill: none; stroke: var(--dieline); stroke-width: 0.8; }
  .fold-line { stroke: var(--fold); stroke-width: 0.7; fill: none; }
  .band-base { fill: var(--navy); }
  .brand-name {
    font-family: "Quicksand", sans-serif;
    font-weight: 300;
    font-size: 17px;
    letter-spacing: 3px;
  }
  .product-line {
    font-family: "Quicksand", sans-serif;
    font-weight: 400;
    text-anchor: middle;
  }
  .vitamin-c .brand-name, .vitamin-c .product-line { fill: var(--silver-text); }
  .anti-aging .brand-name, .anti-aging .product-line { fill: var(--gold-text); }
  .vitamin-c .band-top { fill: url(#silver-sheen); }
  .anti-aging .band-top { fill: url(#gold-sheen); }
</style>
</head>
<body>
<svg class="sheet" viewBox="0 0 1200 754" xmlns="http://www.w3.org/2000/svg">
  <defs>
    <path id="carton-shape" d="M57,237 L93,230 L213,230 L213,215 L222,208 L229,178 L325,178 L325,118 L328,118 L328,100 C328,80 345,62 383,62 C421,62 438,80 438,100 L438,118 L441,118 L441,178 L537,178 L540,195 L548,210 L553,230 L553,578 L545,585 L540,608 L458,608 L448,580 L441,570 L441,556 L325,556 L322,570 L310,580 L305,608 L209,610 L209,668 L206,668 L206,690 C206,710 190,725 151,725 C112,725 96,710 96,690 L96,668 L93,668 L93,556 L57,548 Z"/>
    <clipPath id="carton-clip"><use href="#carton-shape"/></clipPath>
    <linearGradient id="silver-sheen" x1="0" y1="0" x2="1" y2="1">
      <stop offset="0.3" stop-color="var(--silver-light)"/>
      <stop offset="0.75" stop-color="var(--silver-dark)"/>
    </linearGradient>
    <linearGradient id="gold-sheen" x1="0" y1="0" x2="1" y2="1">
      <stop offset="0.2" stop-color="var(--gold-light)"/>
      <stop offset="0.6" stop-color="var(--gold-dark)"/>
    </linearGradient>
    <g id="fold-lines">
      <path class="fold-line" d="M93,230 V556 M209,230 V556 M325,230 V556 M441,230 V556 M93,230 H553 M93,556 H553 M325,178 H441 M325,118 H441 M93,668 H209"/>
    </g>
  </defs>

  <g class="carton vitamin-c">
    <g clip-path="url(#carton-clip)">
      <path class="band-top" d="M40,232 C150,335 420,300 560,160 L560,40 L40,40 Z"/>
      <path class="band-base" d="M80,610 C180,470 420,420 570,500 L570,740 L80,740 Z"/>
    </g>
    <use href="#fold-lines"/>
    <use href="#carton-shape" class="carton-outline"/>
    <text class="brand-name" transform="translate(374,320) rotate(90)">VELORA LABS</text>
    <text class="product-line" x="383" y="504" font-size="13">Vitamin</text>
    <text class="product-line" x="383" y="538" font-size="24" font-weight="300">C</text>
  </g>

  <g class="carton anti-aging" transform="translate(559,-23)">
    <g clip-path="url(#carton-clip)">
      <path class="band-top" d="M40,232 C150,335 420,300 560,160 L560,40 L40,40 Z"/>
      <path class="band-base" d="M80,618 C180,470 420,430 570,500 L570,760 L80,760 Z"/>
    </g>
    <use href="#fold-lines"/>
    <use href="#carton-shape" class="carton-outline"/>
    <text class="brand-name" transform="translate(374,320) rotate(90)">VELORA LABS</text>
    <text class="product-line" x="383" y="506" font-size="12">Anti Aging</text>
    <text class="product-line" x="383" y="530" font-size="17" letter-spacing="2">serum</text>
  </g>
</svg>
</body>
</html>
```